Working Capital graphics

Our business advisory firm requires 9 images to be re-created and improved in the branding of our business.

The 9 images have been uploaded below and the colours and branding of the business can be found at the website www.tallowmereadvisory.com.au

```html
<!DOCTYPE html>
<html lang="en">
<head>
<meta charset="utf-8">
<title>Working Capital</title>
<link rel="stylesheet" href="https://fonts.googleapis.com/css2?family=Montserrat:wght@500;600&display=swap">
<style>
  :root {
    --bg: #ffffff;
    --connector: #9a9a9a;
    --core: #f39322;
    --supply: #172850;
    --process: #223f86;
    --forecast: #1f4e97;
    --customer: #1a5ea9;
    --sku: #147dc0;
    --supplier: #2eaee3;
    --kpi: #67c5ef;
    --it: #9ad7f2;
    --terms: #bde4f4;
    --label: #ffffff;
  }
  html, body {
    margin: 0;
    padding: 0;
    width: 1200px;
    height: 1188px;
    overflow: hidden;
    background: var(--bg);
  }
  .diagram { display: block; width: 1200px; height: 1188px; }
  .connector { stroke: var(--connector); stroke-width: 2; }
  .ring { fill: none; stroke-width: 2; }
  .label {
    font-family: "Montserrat", sans-serif;
    font-weight: 600;
    fill: var(--label);
    text-anchor: middle;
  }
  .label--small { font-size: 20px; letter-spacing: 0.3px; }
  .label--large { font-size: 27px; letter-spacing: 0.5px; }
  .label--core { font-size: 50px; font-weight: 500; letter-spacing: 1.5px; }
</style>
</head>
<body>
<svg class="diagram" viewBox="0 0 1100 1100" xmlns="http://www.w3.org/2000/svg" role="img" aria-label="Working capital and the nine factors that drive it">
  <g class="connectors">
    <line class="connector" x1="555" y1="560" x2="555" y2="198"/>
    <line class="connector" x1="555" y1="560" x2="787" y2="282"/>
    <line class="connector" x1="555" y1="560" x2="912" y2="497"/>
    <line class="connector" x1="555" y1="560" x2="868" y2="741"/>
    <line class="connector" x1="555" y1="560" x2="678" y2="900"/>
    <line class="connector" x1="555" y1="560" x2="431" y2="900"/>
    <line class="connector" x1="555" y1="560" x2="241" y2="741"/>
    <line class="connector" x1="555" y1="560" x2="198" y2="497"/>
    <line class="connector" x1="555" y1="560" x2="322" y2="282"/>
  </g>

  <g class="core">
    <circle cx="555" cy="560" r="190" fill="var(--bg)" class="ring" stroke="var(--core)"/>
    <circle cx="555" cy="560" r="160" fill="var(--core)"/>
    <text class="label label--core" x="555" y="550">WORKING</text>
    <text class="label label--core" x="555" y="600">CAPITAL</text>
  </g>

  <g class="node node--supply">
    <circle cx="555" cy="198" r="108" fill="var(--bg)" class="ring" stroke="var(--supply)"/>
    <circle cx="555" cy="198" r="91" fill="var(--supply)"/>
    <text class="label label--large" x="555" y="180">SUPPLY</text>
    <text class="label label--large" x="555" y="207">CHAIN</text>
    <text class="label label--large" x="555" y="234">ISSUES</text>
  </g>

  <g class="node node--process">
    <circle cx="787" cy="282" r="108" fill="var(--bg)" class="ring" stroke="var(--process)"/>
    <circle cx="787" cy="282" r="91" fill="var(--process)"/>
    <text class="label label--large" x="787" y="278">PROCESS</text>
    <text class="label label--large" x="787" y="305">ISSUES</text>
  </g>

  <g class="node node--forecast">
    <circle cx="912" cy="497" r="108" fill="var(--bg)" class="ring" stroke="var(--forecast)"/>
    <circle cx="912" cy="497" r="91" fill="var(--forecast)"/>
    <text class="label label--small" x="912" y="494">FORECASTING</text>
    <text class="label label--small" x="912" y="514">&amp; PLANNING</text>
  </g>

  <g class="node node--customer">
    <circle cx="868" cy="741" r="108" fill="var(--bg)" class="ring" stroke="var(--customer)"/>
    <circle cx="868" cy="741" r="91" fill="var(--customer)"/>
    <text class="label label--small" x="868" y="738">CUSTOMER</text>
    <text class="label label--small" x="868" y="758">MANAGEMENT</text>
  </g>

  <g class="node node--sku">
    <circle cx="678" cy="900" r="108" fill="var(--bg)" class="ring" stroke="var(--sku)"/>
    <circle cx="678" cy="900" r="91" fill="var(--sku)"/>
    <text class="label label--small" x="678" y="897">SKU</text>
    <text class="label label--small" x="678" y="918">COMPLEXITY</text>
  </g>

  <g class="node node--supplier">
    <circle cx="431" cy="900" r="108" fill="var(--bg)" class="ring" stroke="var(--supplier)"/>
    <circle cx="431" cy="900" r="91" fill="var(--supplier)"/>
    <text class="label label--small" x="431" y="897">SUPPLIER</text>
    <text class="label label--small" x="431" y="917">MANAGEMENT</text>
  </g>

  <g class="node node--kpi">
    <circle cx="241" cy="741" r="108" fill="var(--bg)" class="ring" stroke="var(--kpi)"/>
    <circle cx="241" cy="741" r="91" fill="var(--kpi)"/>
    <text class="label label--small" x="241" y="738">KPIS</text>
    <text class="label label--small" x="241" y="758">&amp; MEASURES</text>
  </g>

  <g class="node node--it">
    <circle cx="198" cy="497" r="108" fill="var(--bg)" class="ring" stroke="var(--it)"/>
    <circle cx="198" cy="497" r="91" fill="var(--it)"/>
    <text class="label label--small" x="198" y="494">IT SYSTEMS &amp;</text>
    <text class="label label--small" x="198" y="514">INFORMATION</text>
  </g>

  <g class="node node--terms">
    <circle cx="322" cy="282" r="108" fill="var(--bg)" class="ring" stroke="var(--terms)"/>
    <circle cx="322" cy="282" r="91" fill="var(--terms)"/>
    <text class="label label--small" x="322" y="279">TERMS &amp;</text>
    <text class="label label--small" x="322" y="299">CONDITIONS</text>
  </g>
</svg>
</body>
</html>
```